Business Card Design

I already have a company logo for my company. I have a logo for the manufacturer we represent. I want a professional business card design.

```html
<!DOCTYPE html>
<html lang="en">
<head>
<meta charset="utf-8">
<title>Business Card – Beacon Signal Works</title>
<link href="https://fonts.googleapis.com/css2?family=Open+Sans:wght@400;700&display=swap" rel="stylesheet">
<style>
  :root {
    --backdrop: #e9e2d8;
    --card: #f6f3ee;
    --card-edge: #ffffff;
    --brand-red: #c8161d;
    --ink: #2a2623;
    --divider: #c8161d;
  }
  * { margin: 0; padding: 0; box-sizing: border-box; }
  html, body {
    width: 1200px; height: 1047px; overflow: hidden;
    background: var(--backdrop);
    font-family: "Open Sans", Arial, sans-serif;
  }
  .business-card {
    position: absolute;
    left: 120px; top: 263px;
    width: 960px; height: 520px;
    background: var(--card);
    border: 2px solid var(--card-edge);
    border-radius: 26px;
    box-shadow: 0 10px 30px rgba(80, 60, 40, 0.12);
  }
  .brand {
    position: absolute;
    left: 40px; width: 420px; top: 210px;
    display: flex; align-items: center; justify-content: center; gap: 14px;
  }
  .brand-mark {
    width: 22px; height: 22px;
    background: var(--brand-red);
  }
  .brand-name {
    font-size: 34px; font-weight: 700;
    color: var(--brand-red);
    line-height: 1.15;
    letter-spacing: 0.5px;
  }
  .divider {
    position: absolute;
    left: 503px; top: 129px;
    width: 2px; height: 260px;
    background: var(--divider);
  }
  .contact-block {
    position: absolute;
    left: 549px; top: 118px;
    color: var(--ink);
  }
  .person-name {
    font-size: 35px; font-weight: 700;
    color: var(--brand-red);
    letter-spacing: 0.5px;
    line-height: 1.2;
  }
  .person-role {
    font-size: 24px; font-weight: 400;
    margin-top: 2px; margin-bottom: 18px;
  }
  .contact-list { list-style: none; }
  .contact-item {
    display: flex; align-items: center; gap: 10px;
    font-size: 24px; line-height: 33px;
  }
  .contact-icon { width: 22px; height: 22px; flex: none; }
  .address {
    font-size: 24px; line-height: 33px;
    margin-top: 14px; font-style: normal;
  }
</style>
</head>
<body>
  <main class="business-card">
    <div class="brand">
      <span class="brand-mark"></span>
      <span class="brand-name">Beacon Signal Works</span>
    </div>

    <div class="divider"></div>

    <section class="contact-block">
      <h1 class="person-name">DANIEL HARPER</h1>
      <p class="person-role">Managing Director</p>
      <ul class="contact-list">
        <li class="contact-item">
          <svg class="contact-icon" viewBox="0 0 24 24" aria-hidden="true">
            <path d="M6.6 10.8a15 15 0 0 0 6.6 6.6l2.2-2.2a1 1 0 0 1 1-.25 11.4 11.4 0 0 0 3.6.6 1 1 0 0 1 1 1V20a1 1 0 0 1-1 1A17 17 0 0 1 3 4a1 1 0 0 1 1-1h3.5a1 1 0 0 1 1 1c0 1.25.2 2.45.6 3.6a1 1 0 0 1-.25 1z" fill="#c8161d"/>
          </svg>
          <span>123 456 789</span>
        </li>
        <li class="contact-item">
          <svg class="contact-icon" viewBox="0 0 24 24" aria-hidden="true">
            <rect x="2" y="5" width="20" height="15" rx="2" fill="#c8161d"/>
            <path d="M3 7l9 6 9-6" stroke="#f6f3ee" stroke-width="1.8" fill="none"/>
          </svg>
          <span>info@harpermail.com</span>
        </li>
        <li class="contact-item">
          <svg class="contact-icon" viewBox="0 0 24 24" aria-hidden="true">
            <circle cx="12" cy="12" r="10" fill="#c8161d"/>
            <path d="M2 12h20M12 2c3 3 3 17 0 20M12 2c-3 3-3 17 0 20" stroke="#f6f3ee" stroke-width="1.4" fill="none"/>
          </svg>
          <span>www.beaconsignal.com</span>
        </li>
      </ul>
      <address class="address">Your address, City<br>State, Zip 1234</address>
    </section>
  </main>
</body>
</html>
```